App Design Project

Hello,
I'm looking for a great designer for my iOS Applications, we have a lot of works and we're short in designers :(
I want to revamp my thermometer iOS app. You will find attached the images I want to replace. I need something with the same element (temp, condition, weather icon) but with a different look!
Same, new icon, you have carte blanche to this one.
I want a design that stands out from the hundreds of weather application that almost all the same design. I am looking for something that does say "wow, it rocks."
Please do not Provide classic design that we can see everywhere ... I'm looking for something with a real artistic choice, contrast, colours, etc.
As a marketing screenshot, I want something classic, you'll find an example attached, feel free to innovate.
To sum-up :
- One new view for my App
- One new icon
- One marketing screenshot
Marketing

```html
<!DOCTYPE html>
<html lang="en">
<head>
<meta charset="utf-8">
<title>Haze – Weather View</title>
<link rel="stylesheet" href="https://fonts.googleapis.com/css2?family=Raleway:wght@200&family=Montserrat:wght@500;700&family=Libre+Baskerville:ital,wght@1,700&display=swap">
<style>
  :root {
    --page-bg: #e3e3e3;
    --tan-top: #b3a57f;
    --tan-bottom: #a8987a;
    --paper-white: #ffffff;
    --paper-shade: #e9e9e9;
    --clay-top: #a8927a;
    --clay-bottom: #a88a7b;
    --clay-light: #c4ada1;
    --ink: #1f1c1a;
    --ink-soft: #2b2622;
    --thin-white: #ffffff;
  }
  html, body {
    margin: 0;
    width: 1200px;
    height: 1200px;
    overflow: hidden;
    background: var(--page-bg);
  }
  .canvas {
    position: relative;
    width: 1200px;
    height: 1200px;
  }
  .app-screen {
    position: absolute;
    left: 292px;
    top: 50px;
    width: 616px;
    height: 1099px;
    display: block;
  }
  .condition { font-family: "Raleway", sans-serif; font-weight: 200; fill: var(--thin-white); }
  .details { font-family: "Montserrat", sans-serif; font-weight: 500; fill: var(--ink-soft); }
  .temp-main, .temp-alt { font-family: "Montserrat", sans-serif; font-weight: 700; fill: var(--ink); }
  .info-mark { font-family: "Libre Baskerville", serif; font-style: italic; font-weight: 700; fill: var(--ink); }
</style>
</head>
<body>
<main class="canvas">
  <svg class="app-screen" viewBox="0 0 428 763" xmlns="http://www.w3.org/2000/svg" aria-label="Weather view: haze, 28 degrees Celsius">
    <defs>
      <linearGradient id="tanFill" x1="0" y1="0" x2="0" y2="1">
        <stop offset="0" stop-color="var(--tan-top)"/>
        <stop offset="1" stop-color="var(--tan-bottom)"/>
      </linearGradient>
      <linearGradient id="clayFill" x1="0" y1="0" x2="0" y2="1">
        <stop offset="0" stop-color="var(--clay-top)"/>
        <stop offset="1" stop-color="var(--clay-bottom)"/>
      </linearGradient>
      <linearGradient id="foldShade" x1="0" y1="0" x2="1" y2="1">
        <stop offset="0" stop-color="#ffffff"/>
        <stop offset="1" stop-color="#e6e6e6"/>
      </linearGradient>
    </defs>

    <!-- paper layers -->
    <rect class="paper-white" x="0" y="0" width="428" height="440" fill="var(--paper-white)"/>
    <polygon class="fold-right" points="300,195 428,100 428,440 300,440" fill="url(#foldShade)"/>
    <rect class="tan-sheet" x="0" y="0" width="300" height="272" fill="url(#tanFill)"/>
    <polygon class="tan-fold" points="300,0 332,0 332,80 300,272" fill="#c6b99a" opacity="0.7"/>
    <polygon class="band-fold-left" points="0,282 70,330 0,400" fill="#ececec"/>
    <polygon class="band-fold-right" points="250,405 428,300 428,405" fill="#f1f1f1"/>

    <!-- lower sheet -->
    <rect class="clay-sheet" x="0" y="405" width="428" height="358" fill="url(#clayFill)"/>
    <polygon class="clay-chevron" points="0,440 300,440 130,595" fill="#a89079"/>
    <polygon class="clay-chevron-edge" points="0,440 130,595 130,570 22,450" fill="#b09a84" opacity="0.6"/>
    <polygon class="clay-strip" points="372,405 428,405 428,600 372,560" fill="var(--clay-light)" opacity="0.8"/>

    <!-- condition block -->
    <text class="condition" x="52" y="155" font-size="70" textLength="192" lengthAdjust="spacingAndGlyphs">HAZE</text>
    <text class="details" x="150" y="224" font-size="17" text-anchor="middle">HUMIDITY: 87%</text>
    <text class="details" x="150" y="250" font-size="17" text-anchor="middle">N/NW AT 8 MPH</text>

    <!-- main temperature -->
    <text class="temp-main" x="48" y="398" font-size="158" letter-spacing="-4">28</text>
    <circle class="degree" cx="258" cy="290" r="10" fill="none" stroke="var(--ink)" stroke-width="4"/>
    <text class="temp-main" x="264" y="358" font-size="96">C</text>

    <!-- divider and refresh -->
    <line class="divider" x1="0" y1="440" x2="370" y2="440" stroke="var(--ink)" stroke-width="1"/>
    <path class="refresh-icon" d="M379,433 A11,11 0 1 1 377,449" fill="none" stroke="var(--ink)" stroke-width="3"/>
    <polygon class="refresh-arrow" points="372,427 386,430 376,440" fill="var(--ink)"/>

    <!-- fahrenheit -->
    <text class="temp-alt" x="52" y="520" font-size="50" letter-spacing="1">82.4</text>
    <circle class="degree" cx="238" cy="479" r="10" fill="none" stroke="var(--ink)" stroke-width="4"/>
    <text class="temp-alt" x="266" y="520" font-size="50">F</text>

    <!-- info -->
    <text class="info-mark" x="372" y="735" font-size="36">i</text>
  </svg>
</main>
</body>
</html>
```